Judicial election website to attract voters

I need a simple one-page web design for a judicial election. I'm going to put up one picture, maybe two. The picture I have needs a little touch-up (whiten teeth for example). I have 3 paragraphs of text. I'd like a "Donate" button that can link to a CoinDrift account. I'd also like a little background design, like the Constitution or something like that. There's a couple other little things but that's the bulk of it.

Target Market(s)

Involved voters and some media

Industry/Entity Type

Legal

Number of Pages Required

1 page

Font styles to use
Sans Serif

Requirements
Must have
• My picture, text, donate button
• Phrase "Remember to vote August 30, 2016!"
Nice to have
• Perhaps a second photo, maybe a short 30 second video of me talking directly to the voters, cool background: Constitution, something judgey.
Should not have
• Not sure ... profanity, I guess.

```html
<!DOCTYPE html>
<html lang="en">
<head>
<meta charset="utf-8">
<title>Town Ballot</title>
<link rel="stylesheet" href="https://fonts.googleapis.com/css2?family=Raleway:wght@600;700&family=Lato:wght@400;700&family=Oswald:wght@400;500&display=swap">
<style>
  :root{
    --navy:#1b2a6b;
    --navy-deep:#14205a;
    --red:#c41230;
    --ink:#3a3a3a;
    --paper:#ffffff;
    --mist:#f0f0f1;
    --black:#0b0b0b;
  }
  *{box-sizing:border-box;margin:0;padding:0}
  html,body{width:772px;height:1200px;overflow:hidden;background:var(--paper)}
  body{font-family:"Lato",sans-serif;color:var(--ink)}
  .page{width:772px;height:1200px;position:relative}

  .topbar{height:62px;position:relative;background:var(--paper)}
  .social{position:absolute;left:63px;top:21px;display:flex;gap:9px}
  .social a{display:block;width:19px;height:19px;border-radius:3px}
  .social a:nth-child(1){background:#3b5a98}
  .social a:nth-child(2){background:#3aa6dd}
  .social a:nth-child(3){background:#1876b0}
  .social a:nth-child(4){background:#d8503d}
  .brand{position:absolute;left:50%;transform:translateX(-50%);top:19px;display:flex;align-items:center;gap:7px;
    font-family:"Raleway",sans-serif;font-weight:700;font-size:20px;letter-spacing:.3px;color:var(--navy);line-height:1;white-space:nowrap}
  .brand .mark{width:13px;height:13px;background:var(--red)}
  .donate{position:absolute;right:65px;top:16px;width:96px;height:30px;background:var(--navy);border-bottom:2px solid var(--red);
    color:#fff;font-family:"Raleway",sans-serif;font-weight:600;font-size:12px;letter-spacing:.5px;
    display:flex;align-items:center;justify-content:center;gap:7px;text-decoration:none}
  .donate .dot{width:11px;height:11px;border:2px solid #fff;border-radius:50%}

  .hero{height:309px;position:relative;overflow:hidden}
  .hero .photo{position:absolute;inset:0;background:linear-gradient(90deg,#ddd8cc 0%,#c9bba4 25%,#8b6a4c 45%,#b7916c 70%,#caa784 100%)}
  .hero .message{position:absolute;left:470px;top:118px;width:240px;text-align:center;
    font-family:"Oswald",sans-serif;font-weight:500;font-size:29px;line-height:38px;letter-spacing:.3px}
  .hero .message .l1{color:var(--navy)}
  .hero .message .l2{color:var(--red)}
  .hero .arrow{position:absolute;top:198px}
  .hero .prev{left:22px}
  .hero .next{right:22px}

  .row{height:245px;display:flex}
  .row > *{width:386px;height:245px;flex:none}
  .panel{position:relative}
  .panel h2{font-family:"Raleway",sans-serif;font-weight:700;font-size:20px;color:var(--navy);letter-spacing:.2px}
  .panel h2 span{color:var(--red)}
  .panel .rule{height:1px;width:305px;margin:8px 0 14px;background:linear-gradient(90deg,var(--red),var(--navy))}
  .panel p{font-size:8.6px;line-height:14.1px;margin-bottom:4px;width:305px}
  .about{padding:30px 0 0 62px}
  .mist{background:var(--mist);padding:30px 0 0 16px}
  .mist p{width:310px}
  .points{padding:30px 0 0 60px}
  .points ul{list-style:none}
  .points li{font-size:8.6px;line-height:20px;display:flex;align-items:center;gap:5px;white-space:nowrap}

  .photo-block{position:relative}
  .video{background:radial-gradient(circle at 50% 50%,#e4e1da 0 32%,#7b6b8a 60%,#3d3f66 100%)}
  .video .play{position:absolute;left:177px;top:100px;width:36px;height:36px;border-radius:50%;background:#fff;
    display:flex;align-items:center;justify-content:center}
  .ballot{background:linear-gradient(90deg,#eee9e0 0%,#d9d4cb 45%,#314275 70%,#b3303a 100%)}
  .tablet{background:linear-gradient(160deg,#c3363d 0%,#d9dbe2 35%,#eef0f4 70%,#9ea5b8 100%)}

  .footer{height:67px;background:var(--navy-deep);position:relative}
  .footer .social{top:25px}
  .footer .brand{top:24px;color:#fff}
  .footer .donate{top:19px;background:var(--red);border-bottom-color:#fff}
  .legal{height:28px;background:var(--black);color:#fff;font-size:8px;display:flex;align-items:center;justify-content:center}
</style>
</head>
<body>
<div class="page">
  <header class="topbar">
    <nav class="social" aria-label="Social links"><a href="#" aria-label="Social link 1"></a><a href="#" aria-label="Social link 2"></a><a href="#" aria-label="Social link 3"></a><a href="#" aria-label="Social link 4"></a></nav>
    <div class="brand"><span class="mark"></span>TOWN BALLOT</div>
    <a class="donate" href="#coindrift"><span class="dot"></span>DONATE</a>
  </header>

  <section class="hero">
    <div class="photo" role="img" aria-label="Voting booths with a flag and the word vote, a voter blurred in the background"></div>
    <svg class="arrow prev" width="22" height="38" viewBox="0 0 22 38"><path d="M20 1 L2 19 L20 37" fill="none" stroke="#fff" stroke-width="1.5"/></svg>
    <div class="message"><div class="l1">REMEMBER TO VOTE</div><div class="l2">AUGUST 30, 2016!</div></div>
    <svg class="arrow next" width="22" height="38" viewBox="0 0 22 38"><path d="M2 1 L20 19 L2 37" fill="none" stroke="#fff" stroke-width="1.5"/></svg>
  </section>

  <section class="row">
    <div class="panel about">
      <h2>ABOUT <span>ME</span></h2>
      <div class="rule"></div>
      <p>Lorem ipsum dolor sit amet, consectetuer adipiscing elit, sed diam nonummy nibh euismod tincidunt ut laoreet dolore magna aliquam erat volutpat. Ut wisi enim ad minim veniam, quis nostrud exerci tation ullamcorper suscipit lobortis nisl ut aliquip ex ea commodo consequat. Duis autem vel eum iriure dolor in hendrerit in vulputate velit esse molestie consequat, vel illum dolore eu feugiat nulla facilisis at vero eros et accumsan et iusto odio dignissim qui blandit praesent luptatum zzril delenit augue duis dolore te feugait nulla facilisi.</p>
      <p>Lusto odio dignissim qui blandit praesent luptatum zzrileti delenit augue duis dolore teleoi feugait nulla dolor in hendrerit in vulputate consequat.Duis autem vel eum iriure dolor in hendrerit in vulputate.</p>
    </div>
    <div class="photo-block video" role="img" aria-label="Video still: hands holding an Elections 2016 sign">
      <div class="play"><svg width="14" height="16" viewBox="0 0 14 16"><path d="M2 1 L13 8 L2 15 Z" fill="#111"/></svg></div>
    </div>
  </section>

  <section class="row">
    <div class="photo-block ballot" role="img" aria-label="A hand dropping an official ballot into a ballot box before a flag"></div>
    <div class="panel mist">
      <h2>LOREM <span>IPSUM</span></h2>
      <div class="rule"></div>
      <p>Lorem ipsum dolor sit amet, consectetuer adipiscing elit, sed diam nonummy nibh euismod tincidunt ut laoreet dolore magna aliquam erat volutpat. Ut wisi enim ad minim veniam, quis nostrud exerci tation ullamcorper suscipit lobortis nisl ut aliquip ex ea commodo consequat. Duis autem vel eum iriure dolor in hendrerit in vulputate velit esse molestie consequat, vel illum dolore eu feugiat nulla facilisis at vero eros et accumsan et iusto odio dignissim qui blandit praesent luptatum zzril delenit augue duis dolore te feugait nulla facilisi.</p>
      <p>Lusto odio dignissim qui blandit praesent luptatum zzrileti delenit augue duis dolore teleoi feugait nulla dolor in hendrerit in vulputate consequat.Duis autem vel eum iriure dolor in hendrerit in vulputate.</p>
    </div>
  </section>

  <section class="row">
    <div class="panel points">
      <h2>LOREM <span>IPSUM</span></h2>
      <div class="rule"></div>
      <ul>
        <li><svg width="12" height="9" viewBox="0 0 12 9"><path d="M1 4.5 H10 M7 1.5 L10 4.5 L7 7.5" fill="none" stroke="#1b2a6b" stroke-width="1.2"/></svg>Lorem ipsum dolor sit amet, consectetuer adipiscing elit, sed diam sit amet</li>
        <li><svg width="12" height="9" viewBox="0 0 12 9"><path d="M1 4.5 H10 M7 1.5 L10 4.5 L7 7.5" fill="none" stroke="#1b2a6b" stroke-width="1.2"/></svg>Lorem ipsum dolor sit amet, consectetuer adipiscing elit</li>
        <li><svg width="12" height="9" viewBox="0 0 12 9"><path d="M1 4.5 H10 M7 1.5 L10 4.5 L7 7.5" fill="none" stroke="#1b2a6b" stroke-width="1.2"/></svg>Lorem ipsum dolor sit amet, consectetuer adipiscing elit, sed diam</li>
        <li><svg width="12" height="9" viewBox="0 0 12 9"><path d="M1 4.5 H10 M7 1.5 L10 4.5 L7 7.5" fill="none" stroke="#1b2a6b" stroke-width="1.2"/></svg>Lorem ipsum dolor sit amet, consectetuer adipiscing elit, sed diam sit amet</li>
        <li><svg width="12" height="9" viewBox="0 0 12 9"><path d="M1 4.5 H10 M7 1.5 L10 4.5 L7 7.5" fill="none" stroke="#1b2a6b" stroke-width="1.2"/></svg>Lorem ipsum dolor sit amet, consectetuer adipiscing elit</li>
        <li><svg width="12" height="9" viewBox="0 0 12 9"><path d="M1 4.5 H10 M7 1.5 L10 4.5 L7 7.5" fill="none" stroke="#1b2a6b" stroke-width="1.2"/></svg>Lorem ipsum dolor sit amet, consectetuer adipiscing elit, sed diam</li>
        <li><svg width="12" height="9" viewBox="0 0 12 9"><path d="M1 4.5 H10 M7 1.5 L10 4.5 L7 7.5" fill="none" stroke="#1b2a6b" stroke-width="1.2"/></svg>Lorem ipsum dolor sit amet, consectetuer adipiscing elit</li>
      </ul>
    </div>
    <div class="photo-block tablet" role="img" aria-label="A finger touching an electronic ballot on a tablet screen"></div>
  </section>

  <footer class="footer">
    <nav class="social" aria-label="Social links"><a href="#" aria-label="Social link 1"></a><a href="#" aria-label="Social link 2"></a><a href="#" aria-label="Social link 3"></a><a href="#" aria-label="Social link 4"></a></nav>
    <div class="brand"><span class="mark"></span>TOWN BALLOT</div>
    <a class="donate" href="#coindrift"><span class="dot"></span>DONATE</a>
  </footer>
  <div class="legal">Copyright © 2016 Town Ballot. All Rights Reserved.</div>
</div>
</body>
</html>
```